Lune Rouge Studio (Masterclasses for Actors) needs artistic and modern website in French & English

Hello!

We need to create a new website (existing : www.lune-rouge-studio.example) for our acting school that holds Masterclasses for professional actors in Paris. It needs to be in French and English with an easy to use back office (wordpress is slow and complicated) (ideas?) so we can add or change workshop dates, upload new photos or videos to the gallery ourselves and make basic changes to the information on line.

Our main clients are French but we have international guests coming who only understand english.

Ideally you would know how to link your creation to the existing domain name, how to make sure the email adresses remain the same and help us find the least expensive but best all in 1 proposition to make it as easy as possible to pay the yearly fee to the hosting platform / web name / etc :-)

Design wise we would like something creative, linked to films etc but without using to many clichés. The logo and a stamp have already been created and we would like to keep these (which has the colours we would like you to use).

It would be nice to maybe have a moving image when you first open the page, maybe the logo itself, something dynamic and visual...

Thank you for you time in reading this!

Margot & Ninon & Apolline
Team LRS

Target Market(s)

actors

Coding

Coded - Design and coding required

Number of Pages Required

5+ page

Font styles to use
Sans Serif

Colors
34a7d8

Requirements
Must have
• able to be read on all electronic devices
Nice to have
• some fun and humour / class
Should not have
• too corporate

```html
<!DOCTYPE html>
<html lang="fr">
<head>
<meta charset="utf-8">
<title>Lune Rouge Studio — Masterclasses pour comédiens</title>
<link rel="stylesheet" href="https://fonts.googleapis.com/css2?family=Lato:wght@300;400;700&display=swap">
<style>
  :root {
    --brand: #34a7d8;
    --brand-deep: #338fd2;
    --ink: #4a4a4a;
    --ink-soft: #6d6d6d;
    --line: #e3e3e3;
    --paper: #ffffff;
    --mist: #efefef;
  }
  * { box-sizing: border-box; margin: 0; padding: 0; }
  html, body { width: 1200px; height: 2449px; overflow: hidden; }
  body { position: relative; background: var(--paper); color: var(--ink); font-family: "Lato", Arial, sans-serif; }
  .abs { position: absolute; }

  /* header */
  .topbar { left: 0; top: 0; width: 1200px; height: 106px; border-bottom: 1px solid var(--line); }
  .contact-mail { left: 201px; top: 57px; font-size: 13px; color: var(--ink); display: flex; align-items: center; gap: 7px; }
  .contact-phone { left: 822px; top: 57px; font-size: 13px; color: var(--ink); display: flex; align-items: center; gap: 6px; }
  .lang { left: 967px; top: 59px; font-size: 10px; color: var(--ink); }
  .lang .on { color: var(--brand); }
  .brand { display: flex; align-items: center; gap: 8px; font-size: 21px; font-weight: 300; color: var(--ink); letter-spacing: 1px; text-transform: uppercase; white-space: nowrap; }
  .brand-dot { width: 14px; height: 14px; border-radius: 50%; background: var(--brand); flex: none; }
  .brand--top { left: 600px; top: 50px; transform: translateX(-50%); }

  .mainnav { left: 0; top: 106px; width: 1200px; height: 65px; display: flex; justify-content: center; align-items: center; gap: 0; }
  .mainnav a { font-size: 13px; color: var(--ink); text-decoration: none; text-transform: uppercase; letter-spacing: .4px; margin: 0 16px; }

  /* hero */
  .hero { left: 0; top: 171px; width: 1200px; height: 507px; background: linear-gradient(100deg, #7a5a3c 0%, #9b7a55 25%, #5e4630 55%, #3a2d22 80%, #2a221c 100%); }
  .hero-veil { left: 0; top: 171px; width: 1200px; height: 507px; background: rgba(0,0,0,.22); }
  .hero-play { left: 558px; top: 342px; }
  .hero-title { left: 0; top: 462px; width: 1200px; text-align: center; font-size: 43px; font-weight: 300; color: #fff; letter-spacing: 1px; }
  .hero-sub { left: 0; top: 523px; width: 1200px; text-align: center; font-size: 14px; color: #fff; }
  .hero-btn { left: 536px; top: 563px; width: 127px; height: 38px; border: 1.5px solid #fff; color: #fff; font-size: 10px; text-transform: uppercase; display: flex; align-items: center; justify-content: center; letter-spacing: .5px; }
  .hero-dots { left: 568px; top: 634px; display: flex; gap: 9px; }
  .hero-dots span { width: 8px; height: 8px; border-radius: 50%; background: #fff; }
  .hero-dots span.on { background: var(--brand); }

  /* quote */
  .quote-band { left: 0; top: 678px; width: 1200px; height: 395px; background: linear-gradient(90deg, #f1f1f1 0%, #ececec 50%, #e6e6e6 100%); }
  .quote-portrait { left: 610px; top: 678px; width: 590px; height: 395px; background: linear-gradient(90deg, rgba(230,230,230,0) 0%, #b9b9b9 25%, #6b6b6b 55%, #3b3b3b 80%, #5a5a5a 100%); }
  .quote-text { left: 201px; top: 826px; font-size: 26px; line-height: 35px; font-weight: 400; color: var(--ink-soft); text-transform: uppercase; letter-spacing: .3px; }
  .quote-author { left: 201px; top: 926px; font-size: 15px; color: var(--brand); text-transform: uppercase; }
  .quote-arrows { left: 201px; top: 1005px; }

  /* portfolio */
  .section-title { left: 0; width: 1200px; text-align: center; font-weight: 300; text-transform: uppercase; }
  .portfolio-title { top: 1128px; font-size: 34px; color: var(--ink); letter-spacing: .5px; }
  .filters { left: 0; top: 1209px; width: 1200px; display: flex; justify-content: center; align-items: center; font-size: 16px; color: var(--ink-soft); text-transform: uppercase; }
  .filters span.sep { margin: 0 14px; color: #999; }
  .filters .on { color: var(--brand); position: relative; }
  .filters .on::after { content: ""; position: absolute; left: -4px; right: -4px; bottom: -11px; height: 2px; background: var(--brand); }
  .tile { width: 252px; height: 177px; }
  .pager-grey { left: 574px; top: 1706px; }

  /* testimonials */
  .voices { left: 0; top: 1777px; width: 1200px; height: 428px; background: var(--brand-deep); }
  .voices-title { top: 1847px; font-size: 23px; color: #fff; letter-spacing: .3px; }
  .voice-text { top: 1932px; width: 388px; font-size: 9px; line-height: 17px; color: #fff; }
  .voice-rule { top: 2046px; width: 388px; height: 1px; background: rgba(255,255,255,.75); }
  .voice-name { top: 2080px; font-size: 12px; color: #fff; text-transform: uppercase; }
  .voices-arrows { left: 574px; top: 2156px; }

  /* footer */
  .brand--foot { left: 600px; top: 2280px; transform: translateX(-50%); }
  .footnav { left: 0; top: 2369px; width: 1200px; display: flex; justify-content: center; font-size: 10px; color: var(--ink); text-transform: uppercase; }
  .footnav span.sep { margin: 0 19px; }
  .copyright { left: 0; top: 2405px; width: 1200px; text-align: center; font-size: 9px; color: var(--ink); text-transform: uppercase; }
</style>
</head>
<body>

<header>
  <div class="abs topbar"></div>
  <div class="abs contact-mail">
    <svg width="11" height="8" viewBox="0 0 11 8"><rect x=".5" y=".5" width="10" height="7" fill="none" stroke="#34a7d8"/><path d="M.5 .5 5.5 4.5 10.5 .5" fill="none" stroke="#34a7d8"/></svg>
    contact@lune-rouge-studio.example
  </div>
  <div class="abs brand brand--top"><span class="brand-dot"></span>Lune Rouge Studio</div>
  <div class="abs contact-phone">
    <svg width="10" height="10" viewBox="0 0 10 10"><path d="M2 0.5 3.6 2.8 2.7 3.8C3.4 5.3 4.7 6.6 6.2 7.3L7.2 6.4 9.5 8 8.6 9.5C4.5 9.5.5 5.5.5 1.4Z" fill="#34a7d8"/></svg>
    +33 6 00 12 34 56
  </div>
  <div class="abs lang"><span class="on">EN</span> | FR</div>

  <nav class="abs mainnav">
    <a>A propos</a><a>Stages</a><a>Photos</a><a>Videos</a><a>Evenements</a><a>L'équipe</a><a>Partenaires</a><a>Blog</a>
  </nav>
</header>

<section>
  <div class="abs hero" role="img" aria-label="Photo de tournage : comédiens autour d'une table de cuisine, équipe technique avec perche et caméra"></div>
  <div class="abs hero-veil"></div>
  <svg class="abs hero-play" width="84" height="84" viewBox="0 0 84 84"><circle cx="42" cy="42" r="40" fill="none" stroke="#fff" stroke-width="2.5"/><path d="M33 26 60 42 33 58Z" fill="#34a7d8"/></svg>
  <h1 class="abs hero-title">STAGE ET FORMATION</h1>
  <p class="abs hero-sub">Neque porro quisquam est qui dolorem ipsum quia dolor sit amet, consectetur, adipisci velit...</p>
  <div class="abs hero-btn">Learn more</div>
  <div class="abs hero-dots"><span class="on"></span><span></span><span></span><span></span></div>
</section>

<section>
  <div class="abs quote-band"></div>
  <div class="abs quote-portrait" role="img" aria-label="Portrait en noir et blanc de l'acteur cité"></div>
  <blockquote class="abs quote-text">The minute that you're not learning<br>I believe you're dead !</blockquote>
  <div class="abs quote-author">— Victor Almeida —</div>
  <svg class="abs quote-arrows" width="26" height="16" viewBox="0 0 26 16"><path d="M6 3 2 8 6 13M20 3 24 8 20 13" fill="none" stroke="#34a7d8" stroke-width="2"/></svg>
</section>

<section>
  <h2 class="abs section-title portfolio-title">Portfolio</h2>
  <div class="filters abs">
    <span class="on">All</span><span class="sep">|</span><span>Coaching</span><span class="sep">|</span><span>Lieu</span><span class="sep">|</span><span>Soirees networking</span><span class="sep">|</span><span>Stages</span>
  </div>

  <div class="abs tile" style="left:201px;top:1282px;background:linear-gradient(160deg,#7aa37a,#5c8fb0 55%,#4d5a4a);" role="img" aria-label="Tournage en extérieur au bord d'une piscine sous un parapluie"></div>
  <div class="abs tile" style="left:475px;top:1282px;background:linear-gradient(160deg,#6a7f3a,#b07a3a 50%,#3e3526);" role="img" aria-label="Photo de groupe des stagiaires dans un jardin en automne"></div>
  <div class="abs tile" style="left:748px;top:1282px;background:linear-gradient(160deg,#e7e3dd,#b8b2aa 50%,#6e6a66);" role="img" aria-label="Séance de travail en noir et blanc, comédiens assis au sol"></div>
  <div class="abs tile" style="left:201px;top:1489px;background:linear-gradient(160deg,#5e8a4a,#c24a3a 40%,#3a3a3a 75%,#7c9a5a);" role="img" aria-label="Équipe de tournage sous des parapluies avec réflecteur"></div>
  <div class="abs tile" style="left:475px;top:1489px;background:linear-gradient(170deg,#7d8a6a,#5e6a55 45%,#6fc4c8 80%,#8fd0d2);" role="img" aria-label="Piscine et façade de la maison du lieu de stage"></div>
  <div class="abs tile" style="left:748px;top:1489px;background:linear-gradient(160deg,#3a3a3a,#9a9a9a 50%,#2a2a2a);" role="img" aria-label="Soirée networking, comédiens posant ensemble en noir et blanc"></div>

  <svg class="abs pager-grey" width="52" height="20" viewBox="0 0 52 20"><path d="M18 2 4 10 18 18Z" fill="#bdbdbd"/><path d="M34 2 48 10 34 18Z" fill="#bdbdbd"/></svg>
</section>

<section>
  <div class="abs voices"></div>
  <h2 class="abs section-title voices-title">Nos comédien(ne)s parlent de Lune Rouge Studio</h2>

  <p class="abs voice-text" style="left:201px">J'ai rencontré Ninon à l'occasion d'un tournage où je devais interpréter un personnage dans une situation extrême, elle m'a non seulement rassurée, fait travailler, mais elle m'a amenée ailleurs... c'est une observatrice pointilleuse.</p>
  <div class="abs voice-rule" style="left:201px"></div>
  <div class="abs voice-name" style="left:201px">Claire Morvan</div>

  <p class="abs voice-text" style="left:609px">J'ai passé trois semaines riches et intenses. Ça m'a fait du bien de revenir travailler avec vous, et approfondir le travail entamé l'an dernier. Je me suis senti plus détendu, plus libre, porté par les intervenants et par mes partenaires. Le groupe était très sympa, plein de talent et d'humour. Un régal. De très jolies rencontres. Merci de nous encadrer et stimuler de la sorte.</p>
  <div class="abs voice-rule" style="left:609px"></div>
  <div class="abs voice-name" style="left:609px">Julien Ferrand</div>

  <svg class="abs voices-arrows" width="52" height="22" viewBox="0 0 52 22"><path d="M12 4 6 11 12 18M40 4 46 11 40 18" fill="none" stroke="#fff" stroke-width="3"/></svg>
</section>

<footer>
  <div class="abs brand brand--foot"><span class="brand-dot"></span>Lune Rouge Studio</div>
  <nav class="abs footnav">
    <span>A propos</span><span class="sep">|</span><span>Stages</span><span class="sep">|</span><span>Photos</span><span class="sep">|</span><span>Videos</span><span class="sep">|</span><span>Evenements</span><span class="sep">|</span><span>L'équipe</span><span class="sep">|</span><span>Partenaires</span><span class="sep">|</span><span>Blog</span>
  </nav>
  <p class="abs copyright">© 2016 Company name &nbsp;|&nbsp; All rights reserved</p>
</footer>

</body>
</html>
```